Looking for a modern, Professional business card design

We have a simple business card, but are looking for a more modern, professional look. A sample of the basic card is attached as well as the logo. We would also like to add that we offer:
Struggling with your finances?
- Learn to become debt free
- Discover the power of cash
- Control your money instead of it controlling you
Let us help you achieve a new level of financial freedom!
Also, we would like to have a "SPECIAL OFFER!: FREE 30 minute consultation"
Financial Planning

```html
<!DOCTYPE html>
<html lang="en">
<head>
<meta charset="utf-8">
<title>Clearpath Money Coaching – Business Card</title>
<link rel="stylesheet" href="https://fonts.googleapis.com/css2?family=Arimo:wght@400;700&family=Archivo:wght@500;700&family=Archivo+Narrow:wght@700&family=Archivo+Black&display=swap">
<style>
  :root{
    --backdrop:#222323;
    --ink:#111111;
    --paper:#ffffff;
    --green:#3f9e3a;
    --green-light:#9fd13c;
    --green-mid:#6dbb3c;
    --green-deep:#2f8a34;
    --text-grey:#3d3d3d;
  }
  *{margin:0;padding:0;box-sizing:border-box}
  html,body{width:1200px;height:987px;overflow:hidden;background:var(--backdrop)}
  .canvas{position:relative;width:1200px;height:987px}

  .card{position:absolute;left:293px;width:615px;height:352px;overflow:hidden}
  .card--front{top:123px;background:var(--paper)}
  .card--back{
    top:499px;
    background:radial-gradient(ellipse 70% 85% at 52% 48%, var(--green-light) 0%, var(--green-mid) 45%, var(--green-deep) 100%);
  }

  .front-swoosh{position:absolute;inset:0;width:615px;height:352px}

  .identity{position:absolute;left:23px;top:18px;font-family:"Arimo",Arial,sans-serif}
  .identity__name{color:var(--green);font-size:26px;font-weight:400;line-height:1.2}
  .identity__title{color:var(--paper);font-size:16px;line-height:1.3;margin-top:2px}

  .brand{position:absolute;left:262px;top:148px;display:flex;align-items:center;gap:14px}
  .brand__dot{width:34px;height:34px;border-radius:50%;background:var(--green);flex:none}
  .brand__name{font-family:"Arimo",Arial,sans-serif;font-weight:700;color:var(--ink);font-size:27px;line-height:1.05;letter-spacing:.5px}

  .contact{position:absolute;right:34px;top:250px;list-style:none;font-family:"Arimo",Arial,sans-serif;font-size:16.5px;color:var(--text-grey);text-align:right}
  .contact li{display:flex;justify-content:flex-end;align-items:center;gap:10px;height:24px}
  .contact svg{width:14px;height:14px;flex:none}

  .pitch{position:absolute;left:45px;top:64px;color:var(--ink)}
  .pitch__heading{font-family:"Archivo",Arial,sans-serif;font-weight:700;font-size:17.5px;letter-spacing:.2px}
  .pitch__list{list-style:none;margin-top:6px;font-family:"Arimo",Arial,sans-serif;font-size:16.5px}
  .pitch__list li{height:26px;padding-left:18px;position:relative;line-height:26px}
  .pitch__list li::before{content:"";position:absolute;left:1px;top:11px;width:5px;height:5px;border-radius:50%;background:var(--ink)}
  .pitch__promise{font-family:"Archivo Narrow",Arial,sans-serif;font-weight:700;font-size:15.5px;margin-top:9px}
  .offer__title{font-family:"Archivo Black",Arial,sans-serif;font-size:41px;line-height:1;margin-top:18px;letter-spacing:.3px}
  .offer__detail{font-family:"Archivo Black",Arial,sans-serif;font-size:19.5px;margin-top:6px;letter-spacing:.3px}
</style>
</head>
<body>
<main class="canvas">

  <section class="card card--front" aria-label="Card front">
    <svg class="front-swoosh" viewBox="0 0 525 300" preserveAspectRatio="none" aria-hidden="true">
      <defs>
        <linearGradient id="bandGreen" x1="0" y1="1" x2="1" y2="0">
          <stop offset="0" stop-color="#5fae35"/>
          <stop offset=".45" stop-color="#9ccf3a"/>
          <stop offset="1" stop-color="#3f9e3a"/>
        </linearGradient>
      </defs>
      <path d="M0,0 L340,0 C210,40 80,140 0,238 Z" fill="#000"/>
      <path d="M340,0 C210,40 80,140 0,238 L0,300 L48,300 C110,180 220,70 345,0 Z" fill="url(#bandGreen)"/>
      <path d="M345,0 C220,70 110,180 48,300" fill="none" stroke="#2f8a34" stroke-width="2"/>
      <path d="M340,0 C230,45 110,140 22,300" fill="none" stroke="#c6e47a" stroke-width="1.2" opacity=".7"/>
    </svg>

    <header class="identity">
      <h1 class="identity__name">Daniel R. Whitfield</h1>
      <p class="identity__title">Personal Financial Coach</p>
    </header>

    <div class="brand">
      <span class="brand__dot"></span>
      <p class="brand__name">CLEARPATH<br>MONEY COACHING</p>
    </div>

    <ul class="contact">
      <li>(555) 014-2290
        <svg viewBox="0 0 14 14"><rect x="3.5" y="0.5" width="7" height="13" rx="1.2" fill="none" stroke="#3f9e3a" stroke-width="1.4"/><rect x="6" y="11" width="2" height="1.2" fill="#3f9e3a"/></svg>
      </li>
      <li>daniel@clearpathmoney.com
        <svg viewBox="0 0 14 14"><rect x="0.5" y="3" width="13" height="9" fill="#3f9e3a"/><path d="M1 3.5 L7 8 L13 3.5" fill="none" stroke="#fff" stroke-width="1.2"/></svg>
      </li>
      <li>www.clearpathmoney.com
        <svg viewBox="0 0 14 14"><circle cx="7" cy="7" r="6.5" fill="#3f9e3a"/><ellipse cx="7" cy="7" rx="2.6" ry="6.5" fill="none" stroke="#fff" stroke-width="1"/><path d="M0.5 7 H13.5" stroke="#fff" stroke-width="1"/></svg>
      </li>
    </ul>
  </section>

  <section class="card card--back" aria-label="Card back">
    <div class="pitch">
      <h2 class="pitch__heading">STRUGGLING WITH YOUR FINANCES?</h2>
      <ul class="pitch__list">
        <li>Learn to become debt free</li>
        <li>Discover the power of cash</li>
        <li>Control your money instead of it controlling you</li>
      </ul>
      <p class="pitch__promise">Let us help you achieve a new level of financial freedom!</p>
      <p class="offer__title">SPECIAL OFFER!</p>
      <p class="offer__detail">FREE 30 MINUTE CONSULTATION</p>
    </div>
  </section>

</main>
</body>
</html>
```